Industrial Project Sign

We need an eye catching (but professional) industrial project sign that will be very large (roughly 12' high x 18' wide). This sign will be highly visible from the adjacent high speed highway.

* The following needs to be at the bottom of the signage: Logo (uploaded), Name (Brightline Property Partners, Inc.) (uploaded) and phone number (415)736-2958

*Name of Project - "Meridale Commerce Park"

* Text items
Land for Sale
Build to Suit
Zoning: Industrial (G I & L I)

* Interesting background that is eye catching
Updates

Good morning all,

We are considering all designers options as we go and are waiting for the final designs to come in by the 4th so that we can give each one a good look.   If you have any new designs, questions, further design options or any tweeks you want to do to current designs, please do so at this time.

Thanks to all of you for your submissions.

Industry/Entity Type

Industrial

```html
<!DOCTYPE html>
<html lang="en">
<head>
<meta charset="utf-8">
<title>Meridale Commerce Park – Project Sign</title>
<link rel="stylesheet" href="https://fonts.googleapis.com/css2?family=Open+Sans:wght@600;700;800&display=swap">
<style>
  :root {
    --maroon: #6b1517;
    --black: #000000;
    --white: #ffffff;
    --band-gray: #6e6e6e;
    --dot-gray: #8c8c8c;
    --text-gray: #555555;
    --ink: #111111;
  }
  * { margin: 0; padding: 0; box-sizing: border-box; }
  html, body { width: 1200px; height: 800px; overflow: hidden; background: var(--white); }
  .sign {
    position: relative; width: 1200px; height: 800px; background: var(--white);
    font-family: "Open Sans", Arial, sans-serif;
  }
  .project-title {
    position: absolute; top: 18px; left: 0; width: 100%; text-align: center;
    font-size: 58px; font-weight: 800; color: var(--ink); letter-spacing: 0.5px; line-height: 1.2;
  }
  .dot-rule {
    position: absolute; left: 78px; width: 1044px; height: 10px;
    background-image:
      radial-gradient(circle, var(--maroon) 3.6px, transparent 4.2px),
      radial-gradient(circle, var(--dot-gray) 3.6px, transparent 4.2px);
    background-size: 40px 10px, 40px 10px;
    background-position: 0 0, 20px 0;
    background-repeat: repeat-x;
  }
  .dot-rule.top { top: 92px; }
  .dot-rule.bottom { top: 707px; }
  .offer-band { position: absolute; top: 133px; left: 0; width: 1200px; height: 83px; }
  .offer-band svg { position: absolute; inset: 0; }
  .offer-text {
    position: absolute; top: 0; height: 83px; line-height: 83px;
    color: var(--white); font-size: 56px; font-weight: 800;
  }
  .offer-text.sale { left: 30px; }
  .offer-text.build { left: 662px; }
  .site-photo {
    position: absolute; top: 216px; left: 0; width: 1200px; height: 217px;
    background: linear-gradient(to bottom, #3f78b8 0%, #7fa8d2 55%, #a9b8a8 80%, #8f9a6e 100%);
  }
  .zoning-band {
    position: absolute; top: 433px; left: 0; width: 1200px; height: 84px;
    background: var(--band-gray); color: var(--white); text-align: center;
    font-size: 54px; font-weight: 800; line-height: 84px;
  }
  .brand-mark {
    position: absolute; top: 560px; left: 330px; width: 80px; height: 80px; background: var(--maroon);
  }
  .company-name {
    position: absolute; top: 580px; left: 475px; font-size: 26px; font-weight: 600; color: var(--text-gray);
    line-height: 1.2;
  }
  .name-rule { position: absolute; top: 618px; left: 473px; width: 446px; height: 3px; background: var(--maroon); }
  .phone {
    position: absolute; top: 618px; left: 470px; font-size: 60px; font-weight: 700; color: var(--black); line-height: 1.2;
  }
  .web {
    position: absolute; top: 728px; left: 0; width: 100%; text-align: center;
    font-size: 46px; font-weight: 800; color: var(--text-gray); line-height: 1.2;
  }
  .web .domain { color: var(--maroon); }
</style>
</head>
<body>
<main class="sign">
  <h1 class="project-title">MERIDALE COMMERCE PARK</h1>
  <div class="dot-rule top"></div>

  <div class="offer-band">
    <svg width="1200" height="83" viewBox="0 0 1200 83" aria-hidden="true">
      <rect x="0" y="0" width="1200" height="83" fill="var(--black)"/>
      <polygon points="0,0 645,0 600,83 0,83" fill="var(--maroon)"/>
    </svg>
    <span class="offer-text sale">LAND FOR SALE</span>
    <span class="offer-text build">BUILD TO SUIT</span>
  </div>

  <div class="site-photo" role="img" aria-label="Panoramic photo of an industrial plant skyline with stacks under a blue sky"></div>

  <div class="zoning-band">ZONING: INDUSTRIAL (G I &amp; L I)</div>

  <div class="brand-mark" aria-hidden="true"></div>
  <p class="company-name">Brightline Property Partners, Inc.</p>
  <div class="name-rule"></div>
  <p class="phone">(415)736-2958</p>

  <div class="dot-rule bottom"></div>
  <p class="web">WWW.<span class="domain">BRIGHTLINEPARTNERS</span>.COM</p>
</main>
</body>
</html>
```